Torvane Halbridge

Looking for modern business cards.
Clean contemporary design.
Similar to this.
https://www.plumvexa-search.example/imgres?imgurl=https%3A%2F%2Fimg.quorlint-cdn.example%2Fsleek_dark_metal_card_design_540.jpg&imgrefurl=https%3A%2F%2Fwww.quorlint-prints.example%2Fsleek_dark_metal_card_design-918273645501928374&q=modern%20business%20cards

But I'd like the blue to look metallic.

Business

```html
<!DOCTYPE html>
<html lang="en">
<head>
<meta charset="utf-8">
<title>Torvane Halbridge – Business Card</title>
<link rel="stylesheet" href="https://fonts.googleapis.com/css2?family=Roboto:wght@400;500;700&display=swap">
<style>
  :root {
    --bg: #dedede;
    --card-light: #f4f4f4;
    --navy: #24566e;
    --navy-deep: #1d4a60;
    --navy-sheen: #2f6a85;
    --accent: #2a9bbd;
    --text: #555555;
    --rule: #8a8a8a;
    --white: #ffffff;
  }
  * { margin: 0; padding: 0; box-sizing: border-box; }
  html, body { width: 1200px; height: 960px; overflow: hidden; }
  body {
    position: relative;
    background: var(--bg);
    font-family: "Roboto", Arial, sans-serif;
  }
  .card { position: absolute; width: 600px; height: 343px; }

  /* Front */
  .card-front { left: 314px; top: 113px; background: var(--card-light); }
  .front-brand {
    position: absolute; right: 86px; top: 66px;
    display: flex; align-items: center; gap: 10px;
  }
  .brand-name {
    font-size: 27px; font-weight: 500; color: var(--navy); white-space: nowrap;
  }
  .brand-dot { width: 12px; height: 12px; border-radius: 50%; background: var(--accent); }
  .name-marker {
    position: absolute; left: 0; top: 150px; width: 16px; height: 40px; background: var(--navy);
  }
  .holder-name {
    position: absolute; left: 39px; top: 149px;
    font-size: 20px; font-weight: 700; color: var(--navy); letter-spacing: 0.2px;
  }
  .holder-title {
    position: absolute; left: 39px; top: 175px;
    font-size: 14.5px; font-weight: 500; color: var(--accent);
  }
  .divider {
    position: absolute; left: 39px; top: 202px; width: 521px; height: 1px; background: var(--rule);
  }
  .contact-list {
    position: absolute; left: 39px; top: 216px; list-style: none;
  }
  .contact-list li {
    display: flex; align-items: center; height: 19px;
    font-size: 14.5px; color: var(--text);
  }
  .contact-list svg { width: 14px; height: 14px; margin-right: 9px; fill: var(--navy); flex: none; }
  .address {
    position: absolute; right: 37px; top: 277px; text-align: right;
    font-size: 14.5px; line-height: 18px; color: var(--text);
  }

  /* Back */
  .card-back {
    left: 311px; top: 472px;
    background: linear-gradient(135deg, var(--navy-deep) 0%, var(--navy) 45%, var(--navy-sheen) 70%, var(--navy) 100%);
  }
  .back-brand {
    position: absolute; left: 0; right: 0; top: 160px;
    display: flex; justify-content: center; align-items: center; gap: 12px;
  }
  .back-brand .brand-name { font-size: 36px; color: var(--white); }
  .back-brand .brand-dot { width: 14px; height: 14px; }
  .back-url {
    position: absolute; left: 0; right: 0; top: 288px; text-align: center;
    font-size: 14.5px; letter-spacing: 2.6px; color: var(--white);
  }
</style>
</head>
<body>

<section class="card card-front" aria-label="Business card front">
  <div class="front-brand">
    <span class="brand-name">Torvane Halbridge</span>
    <span class="brand-dot"></span>
  </div>

  <span class="name-marker"></span>
  <h1 class="holder-name">DALEN ROOKWELL</h1>
  <p class="holder-title">CEO/FOUNDER</p>
  <span class="divider"></span>

  <ul class="contact-list">
    <li>
      <svg viewBox="0 0 24 24" aria-hidden="true"><path d="M6.6 10.8c1.4 2.8 3.8 5.1 6.6 6.6l2.2-2.2c.3-.3.7-.4 1-.2 1.1.4 2.3.6 3.6.6.6 0 1 .4 1 1V20c0 .6-.4 1-1 1C10.6 21 3 13.4 3 4c0-.6.4-1 1-1h3.5c.6 0 1 .4 1 1 0 1.3.2 2.5.6 3.6.1.3 0 .7-.2 1z"/></svg>
      555 014 2538
    </li>
    <li>
      <svg viewBox="0 0 24 24" aria-hidden="true"><path d="M7 1h10c1.1 0 2 .9 2 2v18c0 1.1-.9 2-2 2H7c-1.1 0-2-.9-2-2V3c0-1.1.9-2 2-2zm0 4v13h10V5zm5 14.5a1.2 1.2 0 100 2.4 1.2 1.2 0 000-2.4z"/></svg>
      555 017 9364
    </li>
    <li>
      <svg viewBox="0 0 24 24" aria-hidden="true"><path d="M6 2h12v6H6zM3 9h18c1.1 0 2 .9 2 2v7h-4v4H5v-4H1v-7c0-1.1.9-2 2-2zm4 7v4h10v-4z"/></svg>
      555 019 1940
    </li>
    <li>
      <svg viewBox="0 0 24 24" aria-hidden="true"><path d="M2 5h20v14H2zm2 2v.5l8 5 8-5V7l-8 5z"/></svg>
      hello@halbridge.example
    </li>
    <li>
      <svg viewBox="0 0 24 24" aria-hidden="true"><path d="M12 2a10 10 0 100 20 10 10 0 000-20zm-1 17.9A8 8 0 014.2 10L9 15v1c0 1.1.9 2 2 2zm6.9-2.5c-.3-.8-1-1.4-1.9-1.4h-1v-3c0-.6-.4-1-1-1H8v-2h2c.6 0 1-.4 1-1V7h2c1.1 0 2-.9 2-2v-.4a8 8 0 012.9 12.8z"/></svg>
      www.halbridge.example
    </li>
  </ul>

  <address class="address" style="font-style: normal;">
    4120 Larkspur Row<br>
    Kestrel Falls, Alaska 34590
  </address>
</section>

<section class="card card-back" aria-label="Business card back">
  <div class="back-brand">
    <span class="brand-name">Torvane Halbridge</span>
    <span class="brand-dot"></span>
  </div>
  <p class="back-url">www.torvanehalbridge.example</p>
</section>

</body>
</html>
```